Gemstones e-commerce web-site needs a new template/style

We would like to highlight some of our more exclusive product (gemstones) in a new signature template that has its own style, fonts and colors. The new template would allow for larger and more detailed images. e.g. Tovelcrest.com. The design should account for different sized mobile devices. Current site is http://www.kelvorastones.com

Industry/Entity Type

Product

Number of Pages Required

2 page

```html
<!DOCTYPE html>
<html lang="en">
<head>
<meta charset="utf-8">
<title>Kelvora Stones – Product Details</title>
<link rel="stylesheet" href="https://fonts.googleapis.com/css2?family=Cinzel:wght@400;500&family=Open+Sans:wght@400;600&family=Great+Vibes&display=swap">
<style>
:root{
  --bg:#0b0b0b;
  --bar:#000;
  --footer:#141414;
  --footer-bottom:#0f0f0f;
  --line:#2a2a2a;
  --text:#e6e6e6;
  --muted:#8e8e8e;
  --dim:#6b6b6b;
  --green:#2a9a3c;
  --white:#fff;
}
*{margin:0;padding:0;box-sizing:border-box}
html,body{width:998px;height:1200px;overflow:hidden;background:var(--bg);color:var(--text);font-family:"Open Sans",sans-serif}
.page{position:relative;width:998px;height:1200px}
.header{position:absolute;top:0;left:0;width:998px;height:92px;background:#121212}
.brand{position:absolute;left:84px;top:24px;display:flex;align-items:center;gap:6px}
.brand-mark{width:14px;height:14px;background:var(--green)}
.brand-name{font-size:21px;color:#cfcfcf;font-weight:400;letter-spacing:-.3px}
.brand-tag{position:absolute;left:105px;top:58px;font-size:11px;color:var(--dim)}
.shipping{position:absolute;left:353px;top:27px;width:178px;height:43px;border:1px solid #555;display:flex;align-items:center;justify-content:center;gap:10px;font-family:"Cinzel",serif;font-size:13px;letter-spacing:1px;color:#eee}
.account{position:absolute;right:82px;top:26px;font-size:8px;letter-spacing:1.2px;color:var(--muted);word-spacing:14px}
.social{position:absolute;left:560px;top:56px;font-size:12px;color:#fff;font-weight:600;display:flex;gap:14px}
.phone{position:absolute;left:695px;top:56px;font-size:8.5px;letter-spacing:1px;color:var(--muted);display:flex;align-items:center;gap:8px}
.cart{position:absolute;left:808px;top:50px;font-size:8px;letter-spacing:1.2px;color:var(--muted);display:flex;align-items:center;gap:10px}
.nav{position:absolute;top:92px;left:0;width:998px;height:31px;background:var(--bar);border-bottom:1px solid #1e1e1e;display:flex;align-items:center;justify-content:center;gap:22px;font-family:"Cinzel",serif;font-size:9.5px;letter-spacing:.6px;color:#f0f0f0}
.nav .dot{width:3px;height:3px;background:#ccc;transform:rotate(45deg)}
.hero{position:absolute;top:123px;left:0;width:998px;height:226px;background:linear-gradient(90deg,#121212 0%,#1b1b1b 45%,#2a2a2a 70%,#1a1a1a 100%)}
.hero-art{position:absolute;right:0;top:0;width:500px;height:226px;background:radial-gradient(ellipse at 60% 55%,#8d8d8d 0%,#4a4a4a 35%,#1a1a1a 75%)}
.hero-copy{position:absolute;left:100px;top:30px;width:310px;text-align:center}
.hero-title{font-family:"Cinzel",serif;font-size:17px;color:#fff;letter-spacing:.5px}
.hero-rule{width:96px;height:1px;background:#ddd;margin:16px auto 14px}
.hero-script{font-family:"Great Vibes",cursive;font-size:30px;line-height:31px;color:#fff}
.hero-market{margin-top:14px;font-size:11.5px;color:#fff}
.hero-market b{font-weight:600;color:#e6e6e6}
.product-title{position:absolute;left:82px;top:382px;font-family:"Cinzel",serif;font-size:21px;color:var(--green);letter-spacing:.5px}
.gallery{position:absolute;left:90px;top:446px}
.photo{width:326px;background:radial-gradient(ellipse at 50% 50%,#7fb9c4 0%,#b5d8de 25%,#fff 55%)}
.photo-main{height:296px}
.photo-alt{height:147px;margin-top:10px;background:radial-gradient(ellipse at 50% 100%,#6f8c86 0%,#b9cfca 35%,#fff 65%)}
.scroll{position:absolute;left:424px;top:445px;width:14px;height:455px;background:#262626;border-radius:7px}
.scroll-thumb{position:absolute;left:2px;top:72px;width:10px;height:60px;background:#3a3a3a;border-radius:5px}
.code{position:absolute;left:495px;top:438px;font-family:"Cinzel",serif;font-size:30px;color:#fff}
.desc{position:absolute;left:496px;top:489px;width:390px;font-size:9px;line-height:18px;color:#a9a9a9}
.desc p+p{margin-top:4px}
.footer{position:absolute;top:974px;left:0;width:998px;height:190px;background:var(--footer)}
.footer h3{font-family:"Cinzel",serif;font-weight:400;font-size:13px;letter-spacing:1px;color:#eee}
.about{position:absolute;left:89px;top:36px}
.links{display:grid;grid-template-columns:164px 129px 140px;row-gap:11px;margin-top:13px;font-size:7.3px;letter-spacing:.4px;color:var(--dim);text-transform:uppercase}
.news{position:absolute;left:533px;top:36px}
.news p{margin-top:13px;font-size:7px;letter-spacing:.5px;color:var(--dim)}
.email{margin-top:12px;margin-left:2px;width:224px;height:25px;border:1px solid #666;font-size:7px;letter-spacing:.5px;color:var(--dim);padding:8px 10px}
.subscribe{margin-top:10px;margin-left:2px;width:82px;height:24px;border:1px solid #888;font-size:7.5px;color:#ddd;display:flex;align-items:center;justify-content:center}
.badges{position:absolute;left:808px;top:38px;display:flex;flex-direction:column;gap:10px;align-items:center}
.badge{background:#3c3c3c}
.bottom{position:absolute;top:1164px;left:0;width:998px;height:36px;background:var(--footer-bottom);font-size:7px;letter-spacing:.5px;color:var(--dim)}
.legal{position:absolute;left:91px;top:15px;word-spacing:3px}
.connect{position:absolute;left:643px;top:15px;display:flex;align-items:center;gap:16px}
.connect i{display:block;width:8px;height:8px;border-radius:50%;background:#666}
</style>
</head>
<body>
<div class="page">
  <header class="header">
    <div class="brand"><span class="brand-mark"></span><span class="brand-name">Kelvora Stones</span></div>
    <div class="brand-tag">Cut for Clarity</div>
    <div class="shipping">
      <svg width="46" height="20" viewBox="0 0 46 20"><rect x="10" y="3" width="22" height="11" fill="#2a9a3c"/><path d="M32 6h7l4 4v4H32z" fill="#2a9a3c"/><circle cx="16" cy="16" r="3" fill="#2a9a3c"/><circle cx="37" cy="16" r="3" fill="#2a9a3c"/><path d="M1 6h7M3 9h6M1 12h7" stroke="#2a9a3c" stroke-width="1.4"/></svg>
      FREE SHIPPING
    </div>
    <div class="account">MY ACCOUNT / LOGIN / REGISTER</div>
    <div class="social"><span>Friendwall</span><span>Pixgram</span></div>
    <div class="phone">
      <svg width="11" height="11" viewBox="0 0 24 24"><path d="M6.6 10.8c1.4 2.8 3.8 5.1 6.6 6.6l2.2-2.2c.3-.3.7-.4 1-.2 1.1.4 2.3.6 3.6.6.6 0 1 .4 1 1V20c0 .6-.4 1-1 1C10.6 21 3 13.4 3 4c0-.6.4-1 1-1h3.5c.6 0 1 .4 1 1 0 1.3.2 2.5.6 3.6.1.3 0 .7-.2 1z" fill="#888"/></svg>
      (555) 014-0277
    </div>
    <div class="cart">
      <svg width="18" height="20" viewBox="0 0 18 20"><rect x="1" y="6" width="16" height="13" fill="none" stroke="#888"/><path d="M5 6V4a4 4 0 0 1 8 0v2" fill="none" stroke="#888"/></svg>
      CART IS : 0 ITEMS
    </div>
  </header>

  <nav class="nav">
    <span>HOME</span><span class="dot"></span><span>GEMSTONES</span><span class="dot"></span><span>SHOWS</span><span class="dot"></span><span>SPECIAL GEMSTONES</span><span class="dot"></span><span>CARVINGS</span><span class="dot"></span><span>BEADS</span><span class="dot"></span><span>GOLD JEWELRY</span><span class="dot"></span><span>SILVER JEWELRY</span>
  </nav>

  <section class="hero">
    <div class="hero-art" role="img" aria-label="Close-up of sparkling cut diamonds on a dark reflective surface"></div>
    <div class="hero-copy">
      <div class="hero-title">PRODUCT DETAILS</div>
      <div class="hero-rule"></div>
      <div class="hero-script">Kelvora Stones is a jewellery<br>online boutique</div>
      <div class="hero-market">Kelvora Stones on <b>Bidmarket</b></div>
    </div>
  </section>

  <h1 class="product-title">1.24 CARATS NATURAL AQUAMARINE LOOSE GEMSTONE - OCTAGON</h1>

  <div class="gallery">
    <div class="photo photo-main" role="img" aria-label="Octagon-cut light blue aquamarine on white background"></div>
    <div class="photo photo-alt" role="img" aria-label="Aquamarine gemstone shown from another angle"></div>
  </div>
  <div class="scroll"><div class="scroll-thumb"></div></div>

  <div class="code">KS-110-13-VO</div>
  <div class="desc">
    <p>Aquamarines belong to the Beryl family of gemstones; They are an 8.0 on the Mohs Scale of Hardness. These stones do not chip, crack or scratch easily. They do not require any special treatment and can be worn as ring stones.</p>
    <p>They can be cleaned in any regular jewelry cleaner and will not be affected by low amounts of heat or pressure.</p>
  </div>

  <footer class="footer">
    <div class="about">
      <h3>KELVORA STONES</h3>
      <div class="links">
        <span>Who we are</span><span>Our process</span><span>Our location</span>
        <span>Our history</span><span>Where we operate</span><span>FAQ's</span>
        <span>The concept</span><span>Our promise</span><span>Disclaimers and legal info</span>
        <span>Product showcase</span><span>A quotation form</span><span>News</span>
        <span>A quick education in jewellery</span><span>Our contact</span><span>Blog</span>
      </div>
    </div>
    <div class="news">
      <h3>NEWSLETTER SIGNUP</h3>
      <p>GET OUR RECENT UPDATES THROUGH YOUR EMAIL ID</p>
      <div class="email">ENTER YOUR EMAIL ID</div>
      <div class="subscribe">SUBSCRIBE</div>
    </div>
    <div class="badges">
      <div class="badge" style="width:70px;height:24px"></div>
      <div class="badge" style="width:98px;height:30px"></div>
      <div class="badge" style="width:66px;height:44px"></div>
    </div>
  </footer>
  <div class="bottom">
    <div class="legal">© 2016. KELVORA STONES ALL RIGHTS RESERVED. &nbsp; / &nbsp; TERMS &amp; CONDITIONS &nbsp; / &nbsp; PRIVACY POLICY &nbsp; / &nbsp; DISCLAIMER</div>
    <div class="connect">CONNECT WITH OUR SOCIAL NETWORK : <i></i><i></i><i></i><i></i><i></i></div>
  </div>
</div>
</body>
</html>
```